Business card for Luxury Portable Restroom Trailer company

We are a Luxury Portable Restroom Trailer Company Called FALCRIDGE HIRES. Based in Orange County California. We provide portable restroom trailers for events, such as, Weddings, Concerts, Charity events, Sporting events, Tournaments, Corporate events, ect. We rent and Sell the Luxury restrooms. Our colors are white, grey, and Orange. As you will see in the logo we uploaded.
There are 2 people in the company so the names and titles will change for the 3 people but card will remain the same. Here is the information for each Person: Dwight Penner CFO 555 318-0476
next Person: Leon Marchetti VP 555 318-0476
Next Person: Owen Marchetti CEO 555 318-0476
Information to include on the card: Luxury Restroom Trailers Rental and Sales. Weddings, Concerts, Charity, Sporting and Corp. Events.

```html
<!DOCTYPE html>
<html lang="en">
<head>
<meta charset="utf-8">
<title>Falcridge Hires – Business Card</title>
<link rel="stylesheet" href="https://fonts.googleapis.com/css2?family=Montserrat:wght@400;500;600;700;800&display=swap">
<style>
  :root{
    --orange:#e3692a;
    --card-white:#f4f4f3;
    --card-grey:#575757;
    --ink:#3b3b3b;
    --stage:#1f1f1f;
    --light:#f2f2f2;
  }
  *{box-sizing:border-box;margin:0;padding:0}
  html,body{width:1200px;height:1059px;overflow:hidden}
  body{background:var(--stage);font-family:"Montserrat",sans-serif;position:relative}

  .card{position:absolute;width:690px;height:392px;left:255px}
  .card--front{top:89px;background:var(--card-white)}
  .card--back{top:547px;background:var(--card-grey)}

  .frame{position:absolute;left:22px;right:22px;top:22px;bottom:27px;
    border:2px solid var(--orange);border-bottom:none}
  .frame-foot{position:absolute;left:22px;right:22px;bottom:27px;height:2px;
    display:flex;align-items:center}
  .frame-foot::before,.frame-foot::after{content:"";flex:1;height:2px;background:var(--orange)}
  .frame-foot span{padding:0 9px;white-space:nowrap;transform:translateY(-1px)}

  .brand-name{font-weight:800;color:var(--orange);letter-spacing:.5px;white-space:nowrap}
  .card--front .brand-name{position:absolute;left:76px;width:240px;top:181px;
    font-size:21px;text-align:center}

  .divider{position:absolute;left:343px;top:132px;width:1px;height:130px;background:var(--ink)}

  .person{position:absolute;left:370px;top:125px}
  .person__name{font-size:26px;font-weight:700;color:var(--orange);letter-spacing:.6px;line-height:32px}
  .person__title{font-size:15px;color:var(--ink);margin-top:0;line-height:20px}
  .person__rule{width:12px;height:1.5px;background:var(--orange);margin:9px 0 6px}
  .contact{list-style:none}
  .contact li{display:flex;align-items:center;gap:7px;font-size:16px;color:var(--ink);line-height:27px;margin-left:-2px}
  .contact svg{width:13px;height:13px;flex:none}

  .tagline{position:absolute;left:0;right:0;top:328px;text-align:center;
    font-size:15.5px;font-weight:600;color:var(--orange)}
  .card--front .frame-foot span{font-size:15.5px;color:var(--ink);letter-spacing:.2px}

  .card--back .brand-name{position:absolute;left:0;right:0;top:168px;text-align:center;font-size:42px}
  .card--back .frame-foot span{font-size:15px;color:var(--light);letter-spacing:2.4px;padding:0 14px}
</style>
</head>
<body>

<section class="card card--front" aria-label="Business card front">
  <div class="frame"></div>
  <div class="brand-name">FALCRIDGE HIRES</div>
  <div class="divider"></div>
  <div class="person">
    <h1 class="person__name">OWEN MARCHETTI</h1>
    <p class="person__title">CEO</p>
    <div class="person__rule"></div>
    <ul class="contact">
      <li>
        <svg viewBox="0 0 16 16" aria-hidden="true"><path fill="var(--orange)" d="M3.6 1.2l2.1 2.6c.3.4.3.9 0 1.3L4.6 6.3c.8 2 2.4 3.6 4.4 4.4l1.2-1.1c.4-.3.9-.3 1.3 0l2.6 2.1c.4.3.4.9.1 1.3l-1.1 1.3c-.5.5-1.2.7-1.9.5C6.6 13.6 2.4 9.4 1.2 4.8 1 4.1 1.2 3.4 1.7 2.9L2.9 1.8c.2-.3.5-.5.7-.6z"/></svg>
        555 318-0476
      </li>
      <li>
        <svg viewBox="0 0 16 16" aria-hidden="true"><path fill="var(--orange)" d="M1 6l7-5 7 5v8H1z"/><path fill="var(--card-white)" d="M2.5 6.6L8 10.4l5.5-3.8v6H2.5z" opacity=".9"/><path fill="var(--orange)" d="M2.5 12.6l4-3.3L8 10.4l1.5-1.1 4 3.3z"/></svg>
        owen@falcridgehires.com
      </li>
      <li>
        <svg viewBox="0 0 16 16" aria-hidden="true"><circle cx="8" cy="8" r="7" fill="var(--orange)"/><path fill="var(--card-white)" d="M5 3.5c1 .3 1.6 1.2 1.3 2-.3.7-1.5.6-1.7 1.5-.2.9.9 1.4.6 2.4C4.9 10.2 3.6 10 3 9.3 2.7 6.9 3.5 4.6 5 3.5zM10.5 8.5c1 0 1.8.8 1.5 1.8-.3 1-1.2 1.9-2.2 2.2-.7-.6-.6-1.6-.2-2.4.2-.8.1-1.6.9-1.6z"/></svg>
        www.falcridgehires.com
      </li>
    </ul>
  </div>
  <p class="tagline">Luxury Restroom Trailers Rental and Sales</p>
  <div class="frame-foot"><span>Weddings I Concerts I Charity I Sporting I Corp</span></div>
</section>

<section class="card card--back" aria-label="Business card back">
  <div class="frame"></div>
  <div class="brand-name">FALCRIDGE HIRES</div>
  <div class="frame-foot"><span>www.falcridgehires.com</span></div>
</section>

</body>
</html>
```